Ridgeline Journeys business card

please see website
www.ridgelinejourneys.comau

info needed on card
Curtis Halvey
Ph
email
Adventure Riding GPS trails

please use my logo and colours off my site

Curtis Halvey
curtis@ridgelinejourneys.com

```html
<!DOCTYPE html>
<html lang="en">
<head>
<meta charset="utf-8">
<title>Ridgeline Journeys business card</title>
<link href="https://fonts.googleapis.com/css2?family=Source+Sans+3:ital,wght@0,400;0,600;0,700;1,400;1,600&display=swap" rel="stylesheet">
<style>
  :root {
    --backdrop: #4a4a4a;
    --card-black: #000000;
    --card-white: #f6f6f6;
    --brand-yellow: #f7d117;
    --brand-yellow-deep: #f2b705;
    --ink: #2a2a2a;
    --ink-soft: #4a4a4a;
  }
  * { margin: 0; padding: 0; box-sizing: border-box; }
  html, body { width: 1200px; height: 750px; overflow: hidden; }
  body {
    background: var(--backdrop);
    font-family: "Source Sans 3", sans-serif;
    position: relative;
  }
  .card {
    position: absolute;
    left: 371px;
    width: 461px;
    height: 263px;
    background: var(--card-black);
    box-shadow: 0 2px 6px rgba(0,0,0,0.45);
    overflow: hidden;
  }
  .card-front { top: 99px; }
  .card-back { top: 381px; }
  .front-sweep { position: absolute; inset: 0; width: 100%; height: 100%; }

  .holder-name {
    position: absolute;
    right: 26px;
    top: 20px;
    color: var(--brand-yellow);
    font-size: 17px;
    font-weight: 600;
  }
  .brand {
    position: absolute;
    left: 24px;
    top: 112px;
    display: flex;
    align-items: center;
    gap: 14px;
  }
  .brand-dot {
    width: 36px;
    height: 36px;
    border-radius: 50%;
    background: var(--brand-yellow);
    flex: none;
  }
  .brand-name {
    color: var(--ink);
    font-size: 24px;
    font-weight: 700;
    line-height: 25px;
    text-transform: uppercase;
  }
  .contact-list {
    position: absolute;
    left: 22px;
    top: 195px;
    list-style: none;
  }
  .contact-list li {
    display: flex;
    align-items: center;
    gap: 6px;
    height: 17.5px;
    color: var(--ink-soft);
    font-size: 11.5px;
  }
  .contact-list svg { width: 11px; height: 11px; flex: none; }
  .tagline {
    position: absolute;
    right: 26px;
    top: 228px;
    color: var(--ink-soft);
    font-size: 13px;
    font-style: italic;
    font-weight: 600;
  }

  .back-brand {
    position: absolute;
    left: 0; right: 0;
    top: 108px;
    display: flex;
    justify-content: center;
    align-items: center;
    gap: 12px;
  }
  .back-brand .brand-dot { width: 40px; height: 40px; }
  .back-brand .brand-name {
    color: var(--card-white);
    font-size: 26px;
    line-height: 28px;
  }
  .back-url {
    position: absolute;
    left: 0; right: 0;
    top: 215px;
    text-align: center;
    color: var(--brand-yellow);
    font-size: 11.5px;
    font-style: italic;
  }
</style>
</head>
<body>
  <section class="card card-front">
    <svg class="front-sweep" viewBox="0 0 576 328" preserveAspectRatio="none" aria-hidden="true">
      <defs>
        <linearGradient id="sweepYellow" x1="0" y1="0" x2="1" y2="0">
          <stop offset="0" stop-color="#f7d117"/>
          <stop offset="1" stop-color="#f2b705"/>
        </linearGradient>
      </defs>
      <path d="M0,52 Q260,6 576,168 L576,198 Q260,16 0,58 Z" fill="url(#sweepYellow)"/>
      <path d="M0,58 Q260,16 576,198 L576,328 L0,328 Z" fill="var(--card-white)"/>
    </svg>

    <p class="holder-name">Curtis Halvey</p>

    <div class="brand">
      <span class="brand-dot"></span>
      <p class="brand-name">Ridgeline<br>Journeys</p>
    </div>

    <ul class="contact-list">
      <li>
        <svg viewBox="0 0 24 24"><path fill="#111" d="M6.6 10.8a15.1 15.1 0 0 0 6.6 6.6l2.2-2.2c.3-.3.7-.4 1-.2 1.1.4 2.3.6 3.6.6.6 0 1 .4 1 1V20c0 .6-.4 1-1 1A17 17 0 0 1 3 4c0-.6.4-1 1-1h3.5c.6 0 1 .4 1 1 0 1.3.2 2.5.6 3.6.1.3 0 .7-.2 1z"/></svg>
        614 552 0187
      </li>
      <li>
        <svg viewBox="0 0 24 24"><rect x="2" y="5" width="20" height="14" fill="#111"/><path d="M2 5l10 8 10-8" fill="none" stroke="#f6f6f6" stroke-width="2"/></svg>
        curtis@ridgelinejourneys.com
      </li>
      <li>
        <svg viewBox="0 0 24 24"><circle cx="12" cy="12" r="10" fill="#111"/><path d="M2 12h20M12 2c3 3 3 17 0 20M12 2c-3 3-3 17 0 20" fill="none" stroke="#f6f6f6" stroke-width="1.5"/></svg>
        www.ridgelinejourneys.com.au
      </li>
    </ul>

    <p class="tagline">Adventure Riding GPS trails</p>
  </section>

  <section class="card card-back">
    <div class="back-brand">
      <span class="brand-dot"></span>
      <p class="brand-name">Ridgeline<br>Journeys</p>
    </div>
    <p class="back-url">www.ridgelinejourneys.com.au</p>
  </section>
</body>
</html>
```